Redesign current business card for food company

i would like to redesign my business card. our company is food company, our product range from chips, juices, milk and etc (mostly dried food stuff).
I want o keep same logo but , the rest is open to new design.
you can check at our website about our company www.orvelpantry.com

Target Market(s)

most of food company

Industry/Entity Type

Business

Contact Information for Business Card

I want to keep more to blue color...

Colors
3176b5
abd036

Requirements
Must have
• our old logo
Nice to have
• we do not mind to have nice material on bus card in order to accomplish nice design. for example: using spot uv, embossed and etc.

```html
<!DOCTYPE html>
<html lang="en">
<head>
<meta charset="utf-8">
<title>Orvel Pantry – Business Card</title>
<link href="https://fonts.googleapis.com/css2?family=Open+Sans:wght@400;600;700;800&display=swap" rel="stylesheet">
<style>
  :root {
    --stage-top: #2a2a2a;
    --stage-bottom: #050505;
    --card-white: #ffffff;
    --brand-blue: #1f6fc0;
    --accent-orange: #f5a800;
    --ink: #1b1b1b;
    --warm-yellow: #fbdd1a;
    --warm-orange: #f7961e;
    --wash-yellow: #fdf2c8;
    --wash-green: #e6f2d6;
  }
  html, body {
    margin: 0;
    width: 1200px;
    height: 900px;
    overflow: hidden;
  }
  body {
    background: linear-gradient(180deg, var(--stage-top) 0%, var(--stage-bottom) 100%);
    font-family: "Open Sans", Arial, sans-serif;
    position: relative;
  }
  .card {
    position: absolute;
    top: 184px;
    height: 490px;
    border-radius: 12px;
    overflow: hidden;
  }
  .card-front {
    left: 299px;
    width: 301px;
    background: var(--card-white);
    color: var(--ink);
    text-align: center;
  }
  .card-back {
    left: 645px;
    width: 304px;
    background: linear-gradient(150deg, var(--warm-yellow) 0%, #fcc419 40%, var(--warm-orange) 100%);
  }
  .food-wash-top {
    position: absolute;
    left: 0; top: 36px;
    width: 301px; height: 150px;
    background: radial-gradient(ellipse at 50% 50%, var(--wash-yellow) 0%, rgba(253,242,200,0.5) 55%, rgba(255,255,255,0) 80%);
  }
  .food-wash-bottom {
    position: absolute;
    left: 0; top: 440px;
    width: 301px; height: 190px;
    transform: translateY(-120px);
    background: radial-gradient(ellipse at 50% 60%, var(--wash-green) 0%, rgba(230,242,214,0.45) 50%, rgba(255,255,255,0) 78%);
  }
  .brand-name {
    position: absolute;
    left: 0; right: 0;
    top: 72px;
    margin: 0;
    font-size: 78px;
    font-weight: 800;
    letter-spacing: -2px;
    color: var(--brand-blue);
    line-height: 1;
  }
  .holder {
    position: absolute;
    left: 0; right: 0; top: 243px;
  }
  .holder-name {
    margin: 0;
    font-size: 16px;
    font-weight: 600;
    color: var(--accent-orange);
    line-height: 22px;
  }
  .holder-role {
    margin: 0;
    font-size: 13px;
    line-height: 18px;
  }
  .contacts {
    position: absolute;
    left: 0; right: 0; top: 302px;
    margin: 0; padding: 0;
    list-style: none;
    font-size: 13px;
    line-height: 20.5px;
  }
  .contacts li {
    display: flex;
    justify-content: center;
    align-items: center;
    gap: 6px;
  }
  .contacts svg { width: 10px; height: 10px; flex: none; }
  .company {
    position: absolute;
    left: 0; right: 0; top: 423px;
  }
  .company-name {
    margin: 0;
    font-size: 14px;
    font-weight: 700;
    line-height: 20px;
  }
  .company-address {
    margin: 0;
    font-size: 12.5px;
    line-height: 22px;
  }
  .back-name {
    position: absolute;
    left: 38px;
    top: 350px;
    margin: 0;
    font-size: 84px;
    font-weight: 800;
    letter-spacing: -2px;
    color: var(--card-white);
    line-height: 1;
  }
</style>
</head>
<body>
  <section class="card card-front">
    <div class="food-wash-top" role="img" aria-label="Faint illustration of snacks, fruit and a rainbow behind the brand name"></div>
    <div class="food-wash-bottom" role="img" aria-label="Faint illustration of fruit, trees and a small farm scene"></div>
    <p class="brand-name">orvel</p>

    <div class="holder">
      <p class="holder-name">Marcus Delvaroni</p>
      <p class="holder-role">President</p>
    </div>

    <ul class="contacts">
      <li>
        <svg viewBox="0 0 10 10"><path fill="#f5a800" d="M2 0.5 L3.6 2.4 L2.8 3.6 Q4 6 6.4 7.2 L7.6 6.4 L9.5 8 L8.4 9.5 Q4.5 9.5 0.5 1.6 Z"/></svg>
        <span>555 214 3086</span>
      </li>
      <li>
        <svg viewBox="0 0 10 10"><rect x="0.5" y="3" width="9" height="6" rx="1" fill="#f5a800"/><rect x="2.5" y="0.5" width="5" height="3" fill="#f5a800"/><rect x="2.5" y="5" width="5" height="1.2" fill="#fff"/></svg>
        <span>555 214 3071</span>
      </li>
      <li>
        <svg viewBox="0 0 10 10"><rect x="2.5" y="0.3" width="5" height="9.4" rx="1" fill="#f5a800"/><rect x="3.3" y="1.3" width="3.4" height="6.2" fill="#fff"/></svg>
        <span>555 730 4192</span>
      </li>
      <li>
        <svg viewBox="0 0 10 10"><rect x="0.5" y="2" width="9" height="6.5" fill="#f5a800"/><path d="M0.5 2 L5 5.8 L9.5 2" fill="none" stroke="#fff" stroke-width="0.9"/></svg>
        <span>Marcus@orvelpantry.com</span>
      </li>
      <li>
        <svg viewBox="0 0 10 10"><circle cx="5" cy="5" r="4.5" fill="#f5a800"/><path d="M0.8 5 H9.2 M5 0.6 Q2.5 5 5 9.4 M5 0.6 Q7.5 5 5 9.4" fill="none" stroke="#fff" stroke-width="0.7"/></svg>
        <span>www.orvelpantry.com</span>
      </li>
    </ul>

    <div class="company">
      <p class="company-name">Orvel Enterprises Corp.</p>
      <p class="company-address">2140 E Laurel Ave.Ridgefield CA 91802</p>
    </div>
  </section>

  <section class="card card-back">
    <p class="back-name">orvel</p>
  </section>
</body>
</html>
```